Fine Art business needs new website

We need a simple website with a home page, about us page, New sculptures, Sold sculptures, and a contact us page.Our sculptures are very high end one of a kind pieces. As such we need the site to be VERY elegant and professional. Lastly, because I'll be updating pictures on the website on a monthly basis it needs to be user friendly to update (Wordpress is preferred). The only branding we have so far for the business is a business card.
Updates
I wasn't completely ready when this project launched, also I am on the road right now and haven't been able to be as responsive to all you designers as I would like. I will work on giving feedback to all the top designs we've received so far. Thank you all so much for your participation and hardwork.
Target Market(s)
High end customers (affluent), art collectors, interior decorators/designers
Industry/Entity Type
Art Gallery
Coding
Coded - Design and coding required
Number of Pages Required
5+ page
Requirements
Must have
- Easily editable picture gallery for myself so that I can add new pieces(pictures of the pieces), remove sold pieces, etc. I would like the website to be built in wordpress so I can update it. I currently use mangewordpress through Netmarro for my other business website and would like to do the same for this one.
- Pages:
- -Intro page with featured pieces
- -Current pieces gallery (for sale) mainly a picture gallery
- -Sculptures archive (sold pieces) another picture gallery
- -About us: Pull-down of -about the artist (attached content)
- -Artistic Process (attached content)
- -Show Schedule:
- -one page dedicated to "friends of TMV" (basically a link page)
- TO BE CLEAR "www.pineroverslane.com" IS A TOTALLY DIFFERENT SITE AND I'M NOT TRYING TO COMBINE THE TWO OR JOIN THEM INTO ONE. This page needs be more elegant and seperate from the Pine Rovers site.
- UPDATE: I'd like a link to the TMV Facebook page: https://www.faceplume-social.com/mirelcraftworks/
Nice to have
- I would like the pictures on the gallery pages able to have text connected with them (Materials, price)
- I would like the site style and fonts to be similar to our business cards we've already had designed (picture attached).
Should not have
- Too much flash or other things that will make the site slow to load.

```html
<!DOCTYPE html>
<html lang="en">
<head>
<meta charset="utf-8">
<title>Show Schedule — Tidemere Vale Studios</title>
<link href="https://fonts.googleapis.com/css2?family=Cinzel:wght@400;700&family=Poppins:wght@300;400;500&display=swap" rel="stylesheet">
<style>
:root{
  --ink:#1c1c1c;
  --muted:#8a8a8a;
  --purple:#5a0b9c;
  --purple-dark:#2e1240;
  --lavender:#f3e6fd;
  --white:#ffffff;
  --rule:#cfcfcf;
  --link:#6a1aa8;
}
*{box-sizing:border-box;margin:0;padding:0}
html,body{width:1200px;height:2786px;overflow:hidden;background:var(--white)}
body{position:relative;font-family:"Poppins",sans-serif;color:var(--ink)}
a{text-decoration:none}

.topbar{position:absolute;left:0;top:0;width:1200px;height:186px;border-bottom:1px solid var(--rule)}
.contact-line{position:absolute;left:100px;display:flex;align-items:center;gap:14px;font-size:14px;color:#555;font-weight:300}
.contact-line .ico{width:28px;height:28px;border:1px solid #bbb;border-radius:50%;display:flex;align-items:center;justify-content:center}
.contact-phone{top:10px}
.contact-mail{top:47px}
.brand{position:absolute;left:400px;top:138px;width:400px;text-align:center;font-family:"Cinzel",serif;font-weight:400;font-size:20px;letter-spacing:3px;color:var(--purple-dark)}
.social{position:absolute;display:flex;gap:16px}
.social-top{left:901px;top:5px}
.social-dot{width:38px;height:38px;border-radius:50%;display:flex;align-items:center;justify-content:center}
.dot-a{background:#3f1f8f}.dot-b{background:#7a1f5c}.dot-c{background:#c0261c}.dot-d{background:#1f5fa8}

.nav{position:absolute;left:0;top:186px;width:1200px;height:50px;border-bottom:1px solid var(--rule);font-family:"Cinzel",serif;font-size:14px;color:#222}
.nav span{position:absolute;top:16px}

.hero{position:absolute;left:0;top:236px;width:1200px;height:332px;background:radial-gradient(ellipse at 30% 60%,#6b4a8c 0%,#3a1e52 45%,#1e0d2b 100%)}
.hero h1{position:absolute;width:100%;top:120px;text-align:center;font-family:"Cinzel",serif;font-weight:700;font-size:70px;color:var(--white);letter-spacing:1px}

.schedule{position:absolute;left:0;top:568px;width:1200px;height:1640px;background:var(--lavender)}
.cards{position:absolute;left:98px;top:103px;display:grid;grid-template-columns:repeat(3,313px);grid-auto-rows:327px;column-gap:31px;row-gap:42px}
.card{background:var(--white);position:relative;padding:28px 22px 0}
.badge{display:inline-block;width:121px;height:30px;line-height:30px;text-align:center;background:var(--purple);color:var(--white);font-size:15px;font-weight:500}
.when{margin-top:13px;font-size:12px;color:var(--muted);text-transform:uppercase}
.title{margin-top:10px;font-family:"Cinzel",serif;font-weight:400;font-size:33px;line-height:43px;color:var(--ink)}
.excerpt{margin-top:8px;font-size:13px;line-height:25px;color:#222}
.excerpt.info{color:var(--link);word-break:break-all}
.read-more{position:absolute;left:22px;bottom:24px;font-size:14px;color:#111}
.older{position:absolute;right:102px;top:1519px;font-family:"Cinzel",serif;font-size:13px;text-decoration:underline;color:#222}

.footer-brand{position:absolute;left:400px;top:2378px;width:400px;text-align:center;font-family:"Cinzel",serif;font-weight:400;font-size:16px;letter-spacing:3px;color:var(--purple-dark)}
.footer-title{position:absolute;top:2428px;width:1200px;text-align:center;font-family:"Cinzel",serif;font-weight:400;font-size:29px;color:#222}
.footer-text{position:absolute;top:2476px;left:370px;width:460px;text-align:center;font-size:15px;line-height:27px;color:#222}
.subscribe{position:absolute;left:372px;top:2557px;width:457px;height:45px;display:flex}
.subscribe .field{flex:1;border:1px solid #999;padding-left:14px;line-height:43px;font-size:15px;color:#777}
.subscribe .btn{width:129px;background:var(--purple-dark);color:var(--white);text-align:center;line-height:45px;font-size:15px;letter-spacing:1px}
.social-bottom{left:501px;top:2627px;gap:16px}
.copyright{position:absolute;top:2750px;width:1200px;text-align:center;font-size:12px;color:#555}
</style>
</head>
<body>

<header class="topbar">
  <div class="contact-line contact-phone"><span class="ico"><svg width="12" height="12" viewBox="0 0 24 24"><path fill="#555" d="M6.6 10.8a15.1 15.1 0 0 0 6.6 6.6l2.2-2.2a1 1 0 0 1 1-.25 11.4 11.4 0 0 0 3.6.6 1 1 0 0 1 1 1V20a1 1 0 0 1-1 1A17 17 0 0 1 3 4a1 1 0 0 1 1-1h3.5a1 1 0 0 1 1 1c0 1.25.2 2.45.6 3.6a1 1 0 0 1-.25 1z"/></svg></span>(970) 555-0142</div>
  <div class="contact-line contact-mail"><span class="ico"><svg width="12" height="10" viewBox="0 0 24 18"><path fill="#555" d="M0 0h24v2L12 9 0 2zM0 4l12 7 12-7v14H0z"/></svg></span>hello@pineroverslane.com</div>
  <div class="brand">Tidemere Vale Studios</div>
  <div class="social social-top">
    <span class="social-dot dot-a" role="img" aria-label="Social profile"></span>
    <span class="social-dot dot-b" role="img" aria-label="Photo profile"></span>
    <span class="social-dot dot-c" role="img" aria-label="Social profile"></span>
    <span class="social-dot dot-d"><svg width="16" height="12" viewBox="0 0 24 18"><path fill="#fff" d="M0 0h24v2L12 9 0 2zM0 4l12 7 12-7v14H0z"/></svg></span>
  </div>
</header>

<nav class="nav">
  <span style="left:214px">Home</span>
  <span style="left:322px">About Us</span>
  <span style="left:454px">New Sculptures</span>
  <span style="left:636px">Sold Sculptures</span>
  <span style="left:820px">Contact Us</span>
  <span style="left:970px;top:17px"><svg width="14" height="14" viewBox="0 0 24 24"><circle cx="10" cy="10" r="7" fill="none" stroke="#222" stroke-width="3"/><path d="M15 15l7 7" stroke="#222" stroke-width="3"/></svg></span>
</nav>

<section class="hero" role="img" aria-label="Close-up photograph of purple amethyst crystals">
  <h1>SHOW SCHEDULE</h1>
</section>

<main class="schedule">
  <div class="cards">
    <article class="card"><span class="badge">AUG 2018</span><p class="when">Augest : 11–12</p><h2 class="title">Art Fair Cedar Hollow</h2><p class="excerpt">Lorem ipsum dolor sit amet, consectetur adipiscing elit, sed do eiusmod</p><a class="read-more">Read More</a></article>
    <article class="card"><span class="badge">JUL 2018</span><p class="when">July 21–22</p><h2 class="title">Alderpeak Fine Art Show</h2><p class="excerpt">Lorem ipsum dolor sit amet, consectetur adipiscing elit, sed do eiusmod</p><a class="read-more">Read More</a></article>
    <article class="card"><span class="badge">JUN 2018</span><p class="when">June 9th–10th</p><h2 class="title">Larkfield Park Arts and Music Festival</h2><p class="excerpt info">For more info:</p><a class="read-more">Read More</a></article>

    <article class="card"><span class="badge">MAY 2018</span><p class="when">26th–28th</p><h2 class="title">Willowbend Creek Festival</h2><p class="excerpt info">For more information: http://www.wbcevents.com/willowbend-creek-festival</p><a class="read-more">Read More</a></article>
    <article class="card"><span class="badge">AUG 2018</span><p class="when">Auoust: 2,3,4</p><h2 class="title">Ridgemont Main St Arts Festival</h2><p class="excerpt">Lorem ipsum dolor sit amet, consectetur adipiscing elit, sed do eiusmod</p><a class="read-more">Read More</a></article>
    <article class="card"><span class="badge">JUN 2018</span><p class="when">June 16–17, 23–24, 30–1</p><h2 class="title">Highmesa Renaissance Festival</h2><p class="excerpt info">More info:https://highmesafaire.com/</p><a class="read-more">Read More</a></article>

    <article class="card"><span class="badge">AUG 2018</span><p class="when">August 4–5</p><h2 class="title">Highmesa Renaissance Festival</h2><p class="excerpt">Lorem ipsum dolor sit amet, consectetur</p><a class="read-more">Read More</a></article>
    <article class="card"><span class="badge">JUL 2018</span><p class="when">Festival: 1, 7–8, 14–15, 21–22, 28–29</p><h2 class="title">Highmesa Renaissance Festival</h2><p class="excerpt info">More info:https://highmesafaire.com/</p><a class="read-more">Read More</a></article>
    <article class="card"><span class="badge">MAY 2018</span><p class="when">May 26th–27th in Stapleford, CO</p><h2 class="title">Stapleford Arts Festival</h2><p class="excerpt">Lorem ipsum dolor sit amet, consectetur adipiscing elit, sed do eiusmod</p><a class="read-more">Read More</a></article>

    <article class="card"><span class="badge">SEP 2018</span><p class="when">September : 1–3, 8–9, 15–16, 22–23, 29–30</p><h2 class="title">Northlake Renaissance Festival</h2><p class="excerpt">Northlake Renaissance Festival</p><a class="read-more">Read More</a></article>
  </div>
  <a class="older">OLDER POSTS</a>
</main>

<footer>
  <div class="footer-brand">Tidemere Vale Studios</div>
  <h3 class="footer-title">Get In Touch With Us</h3>
  <p class="footer-text">At vero eos et accusamus et iusto odio dignissimos ducimus qui blanditiis praesentium voluptatum deleniti atque</p>
  <div class="subscribe"><span class="field">Enter Your Email Addresss</span><span class="btn">SUBSCRIBE</span></div>
  <div class="social social-bottom">
    <span class="social-dot dot-a" role="img" aria-label="Social profile"></span>
    <span class="social-dot dot-b" role="img" aria-label="Photo profile"></span>
    <span class="social-dot dot-c" role="img" aria-label="Social profile"></span>
    <span class="social-dot dot-d"><svg width="16" height="12" viewBox="0 0 24 18"><path fill="#fff" d="M0 0h24v2L12 9 0 2zM0 4l12 7 12-7v14H0z"/></svg></span>
  </div>
  <p class="copyright">© Copyrights 2018 Tidemere Vale Studio All Rights Reserved</p>
</footer>

</body>
</html>
```